Need help in designing new business card utilizing our new logo.

BuildMark Solutions works with Construction Business Owners, Managers & IT Professionals to strengthen software usage and increase user productivity.

Our Construction Accounting and Mobile Field Management Software Clients engage with us in the following areas:

New Software Implementations
Software Re-Implementations
Redesigning Software Usage at the User Level
Project Coordination & Management
Continued Software Support

Old tag line:
Planning Clearly - Building Smarter

www.buildmark-solutions.example

Ridge 4 is a product, but not needed for a new business card.

```html
<!DOCTYPE html>
<html lang="en">
<head>
<meta charset="utf-8">
<title>BuildMark Solutions — Business Card</title>
<link rel="stylesheet" href="https://fonts.googleapis.com/css2?family=Jost:wght@400;500&family=Oswald:wght@500&display=swap">
<style>
  :root {
    --backdrop: #222222;
    --card: #262626;
    --ink-light: #f2f2f2;
    --ink-soft: #c9c9c9;
    --ink-grey: #9a9a9a;
    --brand-blue: #3a3fb0;
    --rule: #e6e6e6;
  }
  * { margin: 0; padding: 0; box-sizing: border-box; }
  html, body { width: 1200px; height: 899px; overflow: hidden; background: var(--backdrop); }
  .stage {
    width: 1200px; height: 899px;
    display: flex; flex-direction: column; align-items: center; justify-content: center; gap: 40px;
  }
  .card {
    width: 640px; height: 366px;
    background: var(--card);
    box-shadow: 0 10px 30px rgba(0,0,0,.45);
    position: relative;
    font-family: "Jost", sans-serif;
  }
  /* front */
  .card-front { display: flex; flex-direction: column; align-items: center; justify-content: center; }
  .wordmark-front {
    display: flex; align-items: center; gap: 16px; white-space: nowrap;
    font-size: 40px; font-weight: 500; color: var(--ink-grey); letter-spacing: 1px;
  }
  .wordmark-front .mark-square { width: 34px; height: 34px; background: var(--ink-grey); }
  .tagline {
    position: absolute; bottom: 46px; left: 0; right: 0; text-align: center;
    font-size: 17px; color: var(--ink-soft); letter-spacing: 1px;
  }
  /* back */
  .card-back { display: flex; align-items: center; padding: 0 26px; }
  .wordmark-back {
    width: 270px; flex: none; display: flex; align-items: center; gap: 10px; white-space: nowrap;
    font-size: 24px; font-weight: 500; color: var(--brand-blue);
  }
  .wordmark-back .mark-square { width: 24px; height: 24px; background: var(--brand-blue); flex: none; }
  .divider { width: 2px; height: 250px; background: var(--rule); margin-right: 20px; flex: none; }
  .contact { color: var(--ink-light); white-space: nowrap; }
  .contact-name { font-family: "Oswald", sans-serif; font-size: 32px; font-weight: 500; letter-spacing: .5px; line-height: 1.1; }
  .contact-role { font-size: 18px; color: var(--ink-soft); margin-bottom: 16px; }
  .contact-address { font-size: 15px; line-height: 1.45; margin-bottom: 8px; }
  .contact-list { list-style: none; font-size: 15px; line-height: 1.65; }
  .contact-list li { display: flex; align-items: center; gap: 10px; }
  .contact-list svg { width: 15px; height: 15px; flex: none; }
</style>
</head>
<body>
<main class="stage">
  <section class="card card-front">
    <div class="wordmark-front"><span class="mark-square"></span>BuildMark Solutions</div>
    <p class="tagline">Planning Clearly - Building Smarter</p>
  </section>

  <section class="card card-back">
    <div class="wordmark-back"><span class="mark-square"></span>BuildMark Solutions</div>
    <div class="divider"></div>
    <div class="contact">
      <h1 class="contact-name">DANA R. WHITFIELD</h1>
      <p class="contact-role">Owner</p>
      <p class="contact-address">14 Alder Lane - Suite 310<br>Maple Falls NY 12000</p>
      <ul class="contact-list">
        <li>
          <svg viewBox="0 0 16 16" aria-hidden="true"><path d="M3 1l3 3-1.5 2a9 9 0 0 0 5.5 5.5L12 10l3 3-2 2C6 14 2 10 1 3z" fill="var(--brand-blue)"/></svg>
          800-555-0142 ext.100
        </li>
        <li>
          <svg viewBox="0 0 16 16" aria-hidden="true"><rect x="4" y="1" width="8" height="14" rx="1.5" fill="none" stroke="var(--brand-blue)" stroke-width="1.6"/><circle cx="8" cy="12.5" r="0.9" fill="var(--brand-blue)"/></svg>
          518-555-0187
        </li>
        <li>
          <svg viewBox="0 0 16 16" aria-hidden="true"><rect x="1" y="3" width="14" height="10" fill="var(--brand-blue)"/><path d="M1 3l7 6 7-6" fill="none" stroke="var(--card)" stroke-width="1.4"/></svg>
          dana@buildmark-solutions.example
        </li>
        <li>
          <svg viewBox="0 0 16 16" aria-hidden="true"><circle cx="9.5" cy="6.5" r="4.5" fill="none" stroke="var(--brand-blue)" stroke-width="1.8"/><path d="M6 10l-4.5 4.5" stroke="var(--brand-blue)" stroke-width="2"/></svg>
          www.buildmark-solutions.example
        </li>
      </ul>
    </div>
  </section>
</main>
</body>
</html>
```